Good afternoon,
1. Can we also have the ‘Marblewren selections of the month’ moved to the left side and smaller than the logo quote ‘bright hearts at daybreak’ as it’s just a subheading. That said can we have the ‘Bright hearts at daybreak’ a little larger.
2. Can we have the order of the drop down menus as. Age then Theme then Location (no price). Next to these titles can we have a small image such as a locator point next to ‘location’, two people holding hands adult and child net to ‘age’ and something adventure/city next to ‘theme’, an image to represent the drop down menus. See below:

3. Can we please use this as a logo instead of what we have at the moment. And the same type of setup as what I have here. I really like this map of Australia. We have the rights to it and I have attached it as a file for you to use.

4. Can the selection buttons all be the same blue as the blue in the logo please. Can every part of the page have the logo blue/dirty orange also? Makes it calmer.

5. Could you please add a ‘calendar’ to the tabs (in blue at the top of the page, on the left of ‘add and activity’ .
Let me know how you go. Thanks

Target Market(s)

• Parents and care-givers
• Teachers
• Children (child-friendly)
• Customers are those who ask the question ‘what am I going to do with my child/ren this week/weekend/month’

Industry/Entity Type

Quote

Number of Pages Required

4 page

Font styles to use
Sans Serif

Requirements
Must have
• An ecommerce website (platform) with a responsive system for IOS and Android
• Easy to navigate, user-friendly clean
Nice to have
• some interactive maps
Should not have
• To much clutter/info

```html
<!DOCTYPE html>
<html lang="en">
<head>
<meta charset="utf-8">
<title>Marblewren — Bright hearts at daybreak</title>
<link rel="stylesheet" href="https://fonts.googleapis.com/css2?family=Mukta:wght@400;500;600;700&family=Open+Sans:wght@400;600;700&display=swap">
<style>
:root{
  --blue:#2f7dbf;
  --blue-deep:#1f5f96;
  --orange:#d9834a;
  --ink:#1a1a1a;
  --dark:#222222;
  --darker:#111111;
  --panel:#f5f5f5;
  --line:#dddddd;
  --muted:#555555;
  --white:#ffffff;
  --search:#333333;
}
*{box-sizing:border-box;margin:0;padding:0}
html,body{width:1200px;height:2344px;overflow:hidden;background:var(--white)}
body{position:relative;font-family:"Open Sans",Arial,sans-serif;color:var(--ink)}
.abs{position:absolute}
.heading{font-family:"Mukta",Arial,sans-serif}

/* header */
.brand{left:59px;top:30px;display:flex;align-items:center;gap:12px}
.brand-dot{width:26px;height:26px;border-radius:50%;background:var(--blue)}
.brand-name{font-family:"Mukta",Arial,sans-serif;font-weight:700;font-size:46px;line-height:1;color:var(--blue)}
.btn-blue{background:var(--blue);color:var(--white);font-size:16px;display:flex;align-items:center;justify-content:center;border-radius:2px}
.btn-suggest{left:828px;top:33px;width:160px;height:44px}
.btn-login{left:1000px;top:33px;width:141px;height:44px}

/* nav */
.nav{left:0;top:106px;width:1200px;height:42px;background:var(--ink)}
.nav-item{top:0;height:42px;display:flex;align-items:center;color:var(--white);font-family:"Mukta",Arial,sans-serif;font-weight:600;font-size:16px;letter-spacing:.3px}
.nav-home{left:59px;width:64px;justify-content:center;background:var(--blue)}
.nav-search{left:945px;top:3px;width:196px;height:36px;background:var(--search);color:#ddd;font-size:14px;display:flex;align-items:center;padding-left:12px}
.nav-search svg{position:absolute;right:10px;top:8px}

/* hero */
.hero{left:0;top:148px;width:1200px;height:297px;background:var(--panel)}
.hero-title{top:206px;left:0;width:1200px;text-align:center;font-weight:400;font-size:54px;line-height:1}
.hero-sub{top:270px;left:0;width:1200px;text-align:center;font-size:14px}
.select{top:323px;height:43px;background:var(--white);border:1px solid var(--line);border-radius:2px;display:flex;align-items:center;padding-left:12px;gap:10px;color:#777;font-size:15px}
.select svg.icon{flex:none}
.select .caret{position:absolute;right:14px;top:17px}
.btn-go{left:902px;top:323px;width:220px;height:43px;background:var(--blue);color:var(--white);font-size:19px;display:flex;align-items:center;justify-content:center;border-radius:2px}

/* themes */
.themes{left:0;top:445px;width:1200px;height:539px;background:var(--orange)}
.arrow-box{width:37px;height:33px;background:var(--blue);display:flex;align-items:center;justify-content:center}
.themes-title{top:522px;left:0;width:1200px;text-align:center;color:var(--white);font-weight:600;font-size:42px;line-height:1}
.theme-photo{top:630px;width:231px;height:212px;border:3px solid var(--white)}
.theme-label{top:869px;width:230px;height:47px;background:var(--white);display:flex;align-items:center;justify-content:center;font-family:"Mukta",Arial,sans-serif;font-weight:500;font-size:20px;color:var(--blue-deep)}
.theme-label::before{content:"";position:absolute;left:16px;top:-12px;border-left:12px solid transparent;border-right:12px solid transparent;border-bottom:12px solid var(--white)}

/* suggestions */
.sugg-title{top:1085px;left:59px;width:800px;text-align:left;font-weight:500;font-size:34px;line-height:1;color:var(--blue-deep)}
.card{top:1195px;width:326px;height:425px;background:var(--panel);border:1px solid var(--line)}
.card-photo{left:0;top:0;width:324px;height:222px}
.card-title{left:20px;top:245px;width:290px;font-family:"Mukta",Arial,sans-serif;font-weight:600;font-size:20px;line-height:1.1}
.card-body{left:20px;top:306px;width:296px;font-size:13px;line-height:21px;letter-spacing:-.15px;color:var(--muted)}
.side-arrow{top:1384px;width:33px;height:33px;background:var(--blue);display:flex;align-items:center;justify-content:center}

/* newsletter */
.news{left:0;top:1702px;width:1200px;height:282px;background:var(--panel)}
.news-title{top:1763px;left:0;width:1200px;text-align:center;font-weight:600;font-size:46px;line-height:1}
.news-sub{top:1817px;left:0;width:1200px;text-align:center;font-size:15px}
.news-input{left:377px;top:1877px;width:373px;height:37px;background:var(--white);border:1px solid #999;font-size:14px;color:#888;display:flex;align-items:center;padding-left:12px}
.news-submit{left:750px;top:1877px;width:106px;height:37px;background:var(--blue);color:var(--white);font-weight:700;font-size:16px;display:flex;align-items:center;justify-content:center}

/* footer */
.footer{left:0;top:1984px;width:1200px;height:318px;background:var(--dark)}
.foot-head{top:2035px;font-family:"Mukta",Arial,sans-serif;font-weight:400;font-size:26px;line-height:1;color:var(--white)}
.foot-rule{top:2071px;width:56px;height:4px;background:var(--orange)}
.contact-row{left:59px;display:flex;align-items:center;gap:12px;font-size:14px;color:var(--white)}
.socials{left:59px;top:2187px;display:flex;gap:6px}
.socials span{width:30px;height:30px;border-radius:50%;background:#888}
.services{left:379px;top:2103px;list-style:none;font-size:13.5px;line-height:23.5px;color:var(--white)}
.services li::before{content:"";display:inline-block;width:6px;height:6px;border-radius:50%;background:var(--white);margin-right:10px;vertical-align:middle}
.hours{left:628px;top:2103px;font-size:13.5px;line-height:26px;color:var(--white)}
.map{left:870px;top:2103px;width:255px;height:166px;background:linear-gradient(135deg,#e8e2cf,#d9e3c4 55%,#c7d8e6)}
.copyright{left:0;top:2302px;width:1200px;height:42px;background:var(--darker);color:#ccc;font-size:13px;display:flex;align-items:center;justify-content:center}
</style>
</head>
<body>

<header>
  <div class="abs brand"><span class="brand-dot"></span><span class="brand-name">Marblewren</span></div>
  <div class="abs btn-blue btn-suggest">See our Suggestion</div>
  <div class="abs btn-blue btn-login">Signup/Login</div>
</header>

<nav class="abs nav">
  <div class="abs nav-item nav-home">HOME</div>
  <div class="abs nav-item" style="left:153px">FEATURED ADVENTURES</div>
  <div class="abs nav-item" style="left:365px">CALENDAR</div>
  <div class="abs nav-item" style="left:480px">LIST AN ACTIVITY</div>
  <div class="abs nav-item" style="left:640px">DESTINATION</div>
  <div class="abs nav-search">Search
    <svg width="22" height="22" viewBox="0 0 22 22"><circle cx="9" cy="9" r="6.5" fill="none" stroke="#fff" stroke-width="2.5"/><line x1="14" y1="14" x2="20" y2="20" stroke="#fff" stroke-width="3" stroke-linecap="round"/></svg>
  </div>
</nav>

<section class="abs hero"></section>
<h1 class="abs hero-title heading">Bright hearts at daybreak</h1>
<p class="abs hero-sub">Specific support services for parents and carers are included here</p>

<div class="abs select" style="left:80px;width:261px">
  <svg class="icon" width="24" height="20" viewBox="0 0 24 20"><circle cx="6" cy="3" r="2.6" fill="#2f7dbf"/><path d="M2 20V8a2 2 0 0 1 2-2h4a2 2 0 0 1 2 2v4l4 1v-1a2 2 0 0 1 2-2h2a2 2 0 0 1 2 2v8h-3v-4h-2v4h-3v-5L8 14v6z" fill="#2f7dbf"/><circle cx="17" cy="7.5" r="2" fill="#2f7dbf"/></svg>Age
  <svg class="caret" width="14" height="8" viewBox="0 0 14 8"><path d="M0 0h14L7 8z" fill="#888"/></svg>
</div>
<div class="abs select" style="left:355px;width:259px">
  <svg class="icon" width="22" height="20" viewBox="0 0 22 20"><path d="M0 20V9h5V3h6v6h3V0h5v20z" fill="#2f7dbf"/><rect x="7" y="5" width="2" height="2" fill="#fff"/><rect x="15.5" y="3" width="2" height="2" fill="#fff"/><rect x="15.5" y="8" width="2" height="2" fill="#fff"/><rect x="2" y="12" width="2" height="2" fill="#fff"/></svg>Theme
  <svg class="caret" width="14" height="8" viewBox="0 0 14 8"><path d="M0 0h14L7 8z" fill="#888"/></svg>
</div>
<div class="abs select" style="left:628px;width:261px">
  <svg class="icon" width="14" height="20" viewBox="0 0 14 20"><path d="M7 0a7 7 0 0 1 7 7c0 5-7 13-7 13S0 12 0 7a7 7 0 0 1 7-7z" fill="#2f7dbf"/><circle cx="7" cy="7" r="2.6" fill="#fff"/></svg>Location
  <svg class="caret" width="14" height="8" viewBox="0 0 14 8"><path d="M0 0h14L7 8z" fill="#888"/></svg>
</div>
<div class="abs btn-go">See your suggestion</div>

<section class="abs themes"></section>
<div class="abs arrow-box" style="left:1062px;top:489px"><svg width="18" height="12" viewBox="0 0 18 12"><path d="M17 6H2M7 1 2 6l5 5" stroke="#fff" stroke-width="2.2" fill="none"/></svg></div>
<div class="abs arrow-box" style="left:1104px;top:489px"><svg width="18" height="12" viewBox="0 0 18 12"><path d="M1 6h15M11 1l5 5-5 5" stroke="#fff" stroke-width="2.2" fill="none"/></svg></div>
<h2 class="abs themes-title heading">Explore by theme</h2>

<div class="abs theme-photo" style="left:59px;background:linear-gradient(160deg,#6f9bd0,#c9dcef 45%,#2c3440)" role="img" aria-label="Child looking up at a city landmark tower"></div>
<div class="abs theme-photo" style="left:336px;background:linear-gradient(160deg,#7a2a2a,#3b4a6a 50%,#8a6a3a)" role="img" aria-label="Visitor viewing a wall of historic passports"></div>
<div class="abs theme-photo" style="left:619px;background:linear-gradient(180deg,#5b4a2e,#8a6b3e 55%,#c48a4a)" role="img" aria-label="Gallery room hung with framed paintings"></div>
<div class="abs theme-photo" style="left:902px;background:linear-gradient(160deg,#3d4a2a,#6b7a4a 50%,#4a3a2a)" role="img" aria-label="Child walking through a mossy rainforest"></div>

<div class="abs theme-label" style="left:59px">Explore Icons</div>
<div class="abs theme-label" style="left:340px">Explore History</div>
<div class="abs theme-label" style="left:619px">Explore the Arts</div>
<div class="abs theme-label" style="left:908px">Explore Nature</div>

<h2 class="abs sugg-title heading">Marblewren selections of the month</h2>

<article class="abs card" style="left:59px">
  <div class="abs card-photo" style="background:linear-gradient(170deg,#a9c7e8,#7fa05a 50%,#5b7a3a)" role="img" aria-label="Two children running a trail race outdoors"></div>
  <h3 class="abs card-title">Concert of classical music and stories told</h3>
  <p class="abs card-body">Lorem Ipsum has been the industry's standard dummy text ever since the 1500s, when an unknown printer took a galley of type and scrambled it to make a type specimen book.</p>
</article>
<article class="abs card" style="left:441px">
  <div class="abs card-photo" style="background:linear-gradient(180deg,#e9e3d8,#c9bba4 60%,#7a3a2a)" role="img" aria-label="Child playing captain with a ship's wheel and treasures"></div>
  <h3 class="abs card-title" style="top:255px">Concert of classical music and stories told</h3>
  <p class="abs card-body" style="top:316px">Lorem Ipsum has been the industry's standard dummy text ever since the 1500s, when an unknown printer took a galley of type and scrambled it to make a type specimen book.</p>
</article>
<article class="abs card" style="left:811px">
  <div class="abs card-photo" style="background:linear-gradient(160deg,#e8d8d0,#d98aa8 50%,#a07a6a)" role="img" aria-label="Children making colourful craft puppets"></div>
  <h3 class="abs card-title" style="top:255px">Concert of classical music and stories told</h3>
  <p class="abs card-body" style="top:316px">Lorem Ipsum has been the industry's standard dummy text ever since the 1500s, when an unknown printer took a galley of type and scrambled it to make a type specimen book.</p>
</article>

<div class="abs side-arrow" style="left:0"><svg width="16" height="12" viewBox="0 0 16 12"><path d="M15 6H2M6 1 1 6l5 5" stroke="#fff" stroke-width="2.2" fill="none"/></svg></div>
<div class="abs side-arrow" style="left:1167px"><svg width="16" height="12" viewBox="0 0 16 12"><path d="M1 6h13M10 1l5 5-5 5" stroke="#fff" stroke-width="2.2" fill="none"/></svg></div>

<section class="abs news"></section>
<h2 class="abs news-title heading">Get started with our Newsletter</h2>
<p class="abs news-sub">Free shipping, phenomenal customer service and wicked prices.</p>
<div class="abs news-input">Enter your Email here</div>
<div class="abs news-submit">Submit</div>

<footer class="abs footer"></footer>
<h4 class="abs foot-head" style="left:59px">Contact us</h4>
<div class="abs foot-rule" style="left:59px"></div>
<h4 class="abs foot-head" style="left:375px">Our Services</h4>
<div class="abs foot-rule" style="left:375px"></div>
<h4 class="abs foot-head" style="left:628px">Store Hours</h4>
<div class="abs foot-rule" style="left:628px"></div>
<h4 class="abs foot-head" style="left:870px">Our Location</h4>
<div class="abs foot-rule" style="left:870px"></div>

<div class="abs contact-row" style="top:2107px">
  <svg width="18" height="18" viewBox="0 0 18 18"><path d="M4 1l3 4-2 2c1 3 3 5 6 6l2-2 4 3-2 3C8 17 1 10 1 3z" fill="#fff"/></svg>0355 014 282
</div>
<div class="abs contact-row" style="top:2140px">
  <svg width="18" height="13" viewBox="0 0 18 13"><rect x="0.5" y="0.5" width="17" height="12" fill="#fff"/><path d="M1 1l8 6 8-6" stroke="#222" stroke-width="1.4" fill="none"/></svg>hello@marblewren.example
</div>
<div class="abs socials"><span></span><span></span><span></span><span></span></div>

<ul class="abs services">
  <li>Home</li><li>About Us</li><li>News</li><li>Free Tests</li><li>Larkfield Stores</li><li>Community</li><li>Courses</li>
</ul>

<div class="abs hours">
  Monday:10am - 8pm<br>Tuesday:10am - 7pm<br>Wednesday:10am - 8pm<br>Thrusday: 10am - 8pm<br>Friday:10am - 8pm<br>Saturday:10am - 7pm
</div>

<div class="abs map" role="img" aria-label="Street map of Melbourne with a pin marking the Marblewren location"></div>

<div class="abs copyright">© 2016 Copyright Marblewren. All Right Reserved</div>

</body>
</html>
```